Business Card Design

We need a business card designed for our new company. Prefer a black card with white logo & writing.

Contact Information for Business Card

Ted Galloway, address: 7-4812 Fernhollow Road, Abbotsford, BC, V3K 8R2, Office Phone: 604-712-3390, Cell: 604-947-2164, Email: ted@resinworkshub.ca

Colors

Designer to choose only greyscale colors for use in the design.

```html
<!DOCTYPE html>
<html lang="en">
<head>
<meta charset="utf-8">
<title>Resin Works Hub — Business Card</title>
<link href="https://fonts.googleapis.com/css2?family=Poppins:wght@400;600;700&display=swap" rel="stylesheet">
<style>
  :root{
    --page:#d2d2d2;
    --card:#231f1e;
    --band:#7b7b7b;
    --ink:#ffffff;
    --rule:#5a5554;
    --peak-a:#6a5a52;
    --peak-b:#2b2523;
  }
  *{margin:0;padding:0;box-sizing:border-box}
  html,body{width:1200px;height:800px;overflow:hidden}
  body{background:var(--page);font-family:"Poppins",sans-serif;color:var(--ink);position:relative}
  .card{position:absolute;left:337px;width:525px;height:300px;background:var(--card);border-radius:18px;overflow:hidden;box-shadow:0 6px 18px rgba(0,0,0,.25)}
  .card--front{top:70px}
  .card--back{top:430px}

  .front__band{position:absolute;top:0;bottom:0;left:330px;width:110px;background:var(--band)}
  .brand{position:absolute;display:flex;align-items:center;gap:8px;font-weight:700;letter-spacing:.5px;color:var(--ink);text-transform:uppercase;white-space:nowrap}
  .brand__dot{border-radius:50%;background:var(--ink);flex:none}
  .front__brand{left:280px;width:210px;top:130px;font-size:18px;justify-content:center}
  .front__brand .brand__dot{width:14px;height:14px}

  .contact{position:absolute;left:38px;top:54px;width:240px}
  .contact__name{font-weight:700;font-size:21px;letter-spacing:.5px;text-transform:uppercase}
  .contact__rule{width:34px;height:1px;background:var(--rule);margin:14px 0 12px}
  .contact__list{list-style:none;font-size:14px;line-height:21px}
  .contact__list li{display:flex;align-items:center;gap:9px}
  .contact__list svg{width:12px;height:12px;flex:none;fill:var(--ink)}
  .contact__address{font-size:14px;line-height:21px}

  .back__peaks{position:absolute;left:0;top:0;width:525px;height:110px;background:linear-gradient(180deg,var(--peak-a),var(--peak-b) 80%,var(--card))}
  .back__brand{left:0;right:0;top:172px;justify-content:center;font-size:32px;gap:10px}
  .back__brand .brand__dot{width:22px;height:22px}
</style>
</head>
<body>
  <section class="card card--front" aria-label="Card front">
    <div class="front__band"></div>
    <div class="brand front__brand"><span class="brand__dot"></span>Resin Works Hub</div>
    <div class="contact">
      <h1 class="contact__name">Ted Galloway</h1>
      <div class="contact__rule"></div>
      <ul class="contact__list">
        <li><svg viewBox="0 0 24 24"><path d="M6.6 10.8a15 15 0 0 0 6.6 6.6l2.2-2.2c.3-.3.7-.4 1-.2 1.1.4 2.3.6 3.6.6.6 0 1 .4 1 1V20c0 .6-.4 1-1 1A17 17 0 0 1 3 4c0-.6.4-1 1-1h3.5c.6 0 1 .4 1 1 0 1.3.2 2.5.6 3.6.1.3 0 .7-.2 1z"/></svg>604-712-3390</li>
        <li><svg viewBox="0 0 24 24"><path d="M7 1h10a2 2 0 0 1 2 2v18a2 2 0 0 1-2 2H7a2 2 0 0 1-2-2V3a2 2 0 0 1 2-2zm0 3v15h10V4z"/></svg>604-947-2164</li>
        <li><svg viewBox="0 0 24 24"><path d="M2 4h20v16H2zm2 2v.5l8 5.5 8-5.5V6z"/></svg>ted@resinworkshub.ca</li>
      </ul>
      <div class="contact__rule"></div>
      <p class="contact__address">7-4812 Fernhollow Road,<br>Abbotsford, BC, V3K 8R2</p>
    </div>
  </section>

  <section class="card card--back" aria-label="Card back">
    <div class="back__peaks" role="img" aria-label="Mountain range silhouette in dark brown-grey"></div>
    <div class="brand back__brand"><span class="brand__dot"></span>Resin Works Hub</div>
  </section>
</body>
</html>
```